Personal training and nutrition business needs business card design

We need a business card that outlays our services and invites potential customers to join our team and take the first step to a healthier and more enjoyable life. We cater for any level of fitness and specialize in weight loss and conditioning, strength training, muscle gain and strength endurance. Whether you are just starting off or need some help getting to the next level of your journey we are here to get the job done.
We specialize in one on one or one on two personal training sessions and each program will be custom made to suit individual fitness goals of our clients

```html
<!DOCTYPE html>
<html lang="en">
<head>
<meta charset="utf-8">
<title>Pulse &amp; Pace – Business Card</title>
<link rel="stylesheet" href="https://fonts.googleapis.com/css2?family=Questrial&display=swap">
<style>
  :root {
    --stage: #2c2c2c;
    --purple-deep: #6f46a0;
    --purple-mid: #9a55a6;
    --purple-light: #b464a8;
    --purple-text: #8a4da6;
    --ink: #1a1a1a;
    --paper: #ffffff;
    --mist: #ececec;
    --rule: #d6d6d6;
  }
  * { box-sizing: border-box; margin: 0; padding: 0; }
  html, body { width: 1200px; height: 866px; overflow: hidden; }
  body {
    background: var(--stage);
    font-family: "Questrial", "Century Gothic", sans-serif;
    display: flex;
    align-items: center;
    justify-content: center;
    gap: 40px;
  }
  .card {
    width: 540px;
    height: 309px;
    position: relative;
    overflow: hidden;
    box-shadow: 0 10px 24px rgba(0,0,0,.45);
  }

  /* Front */
  .card-front {
    background: linear-gradient(135deg, var(--purple-deep) 0%, var(--purple-light) 48%, var(--purple-mid) 100%);
    color: var(--paper);
    display: flex;
    flex-direction: column;
    align-items: center;
    justify-content: center;
    text-align: center;
  }
  .brand {
    display: flex;
    align-items: center;
    gap: 12px;
    font-size: 40px;
    letter-spacing: 1px;
    text-transform: uppercase;
  }
  .brand-dot {
    width: 22px; height: 22px;
    border-radius: 50%;
    background: currentColor;
  }
  .brand-tagline {
    margin-top: 8px;
    font-size: 9px;
    letter-spacing: 1.6px;
    text-transform: uppercase;
  }
  .services {
    margin-top: 26px;
    font-size: 15px;
    line-height: 1.45;
  }

  /* Back */
  .card-back {
    background:
      linear-gradient(100deg, var(--mist) 0%, rgba(236,236,236,.6) 35%, rgba(255,255,255,0) 60%),
      var(--paper);
    color: var(--ink);
  }
  .person {
    position: absolute;
    left: 34px; top: 42px;
  }
  .person-name {
    color: var(--purple-text);
    font-size: 23px;
    text-transform: uppercase;
    letter-spacing: .5px;
  }
  .person-role { font-size: 14px; margin-top: 2px; }
  .contact-list {
    list-style: none;
    margin-top: 16px;
    font-size: 14px;
    line-height: 1.5;
  }
  .contact-list li { display: flex; align-items: center; gap: 7px; }
  .contact-icon { width: 12px; height: 12px; fill: var(--purple-text); flex: none; }
  .web-name { color: var(--purple-text); }

  .card-back .brand-block {
    position: absolute;
    right: 34px; top: 64px;
    text-align: right;
  }
  .card-back .brand { color: var(--ink); font-size: 30px; justify-content: flex-end; }
  .card-back .brand-dot { background: var(--purple-text); width: 18px; height: 18px; }
  .card-back .brand-tagline { color: var(--purple-text); margin-top: 6px; }

  .divider {
    position: absolute;
    left: 190px; right: 34px; top: 196px;
    height: 1px;
    background: var(--rule);
  }
  .address {
    position: absolute;
    right: 34px; bottom: 34px;
    text-align: right;
    font-size: 14px;
    line-height: 1.45;
  }
</style>
</head>
<body>

  <section class="card card-front" aria-label="Card front">
    <div class="brand"><span class="brand-dot"></span>Pulse &amp; Pace</div>
    <p class="brand-tagline">Personal training. Nutrition. Motivation</p>
    <p class="services">
      Weight loss &amp; Conditioning • Strength Training<br>
      Muscle Gain • Strength Endurance
    </p>
  </section>

  <section class="card card-back" aria-label="Card back">
    <div class="person">
      <h1 class="person-name">Daniel Reyes</h1>
      <p class="person-role">Managing Director</p>
      <ul class="contact-list">
        <li>
          <svg class="contact-icon" viewBox="0 0 24 24" aria-hidden="true"><path d="M6.6 10.8a15 15 0 0 0 6.6 6.6l2.2-2.2a1 1 0 0 1 1-.25 11.4 11.4 0 0 0 3.6.57 1 1 0 0 1 1 1V20a1 1 0 0 1-1 1A17 17 0 0 1 3 4a1 1 0 0 1 1-1h3.5a1 1 0 0 1 1 1c0 1.25.2 2.45.57 3.57a1 1 0 0 1-.25 1z"/></svg>
          044-555 010 200
        </li>
        <li>
          <svg class="contact-icon" viewBox="0 0 24 24" aria-hidden="true"><path d="M2 5h20v14H2zm2 2v.4l8 5 8-5V7z"/></svg>
          info@pulsepace.com
        </li>
        <li>
          <svg class="contact-icon" viewBox="0 0 24 24" aria-hidden="true"><circle cx="12" cy="12" r="10"/><path d="M2 12h20M12 2c3 3 3 17 0 20M12 2c-3 3-3 17 0 20" stroke="#fff" stroke-width="1.4" fill="none"/></svg>
          <span>www.<span class="web-name">pulsepace</span>.com</span>
        </li>
      </ul>
    </div>

    <div class="brand-block">
      <div class="brand"><span class="brand-dot"></span>Pulse &amp; Pace</div>
      <p class="brand-tagline">Personal training. Nutrition. Motivation</p>
    </div>

    <div class="divider"></div>

    <p class="address">
      421, Address line goes here<br>
      45452, Country Name
    </p>
  </section>

</body>
</html>
```